Corvanta Group business card redesign

Please throw away what we have and start from scratch. We are bored with our Corvanta Group cards, they need a refresh and as we have introduced a new company to the fold it is the perfect time. Please come up with something that pops. Finishes like foil embossing or engraving are all on the table. Please not be afraid to turn it on it's head. Creative people only.
Target Market(s)
From engineers, to builders, to DIY
Industry/Entity Type
Manufacturer
Contact Information for Business Card
Double sided
Colors
9bcb3c
0255a3
0592cd
Requirements
Must have
- All logos must be shown, the four company logs can be on the back. The group logo is the only one that must be on the front. .
Nice to have
- a design that will age well, we are looking for at least 5 years from the cards.
Should not have
- Please do not send me designs which are just templates that are on the internet, you will be wasting your and my time. As I have searched and searched online and have not found anything I like.

```html
<!DOCTYPE html>
<html lang="en">
<head>
<meta charset="utf-8">
<title>Corvanta Group – Business Card</title>
<link href="https://fonts.googleapis.com/css2?family=Open+Sans:wght@400;600;700&display=swap" rel="stylesheet">
<style>
  :root {
    --navy: #233c84;
    --green: #80c242;
    --white: #ffffff;
    --ink: #233c84;
    --backdrop: #e9e7e4;
    --card-shadow: 0 10px 30px rgba(0,0,0,0.18);
  }
  * { margin: 0; padding: 0; box-sizing: border-box; }
  html, body {
    width: 1200px; height: 900px; overflow: hidden;
    background: var(--backdrop);
    font-family: "Open Sans", Arial, sans-serif;
  }
  .canvas { position: relative; width: 1200px; height: 900px; }

  /* Front */
  .card-front {
    position: absolute; left: 78px; top: 34px;
    width: 588px; height: 364px;
    background: var(--navy);
    overflow: hidden;
    box-shadow: var(--card-shadow);
  }
  .card-front .swoosh { position: absolute; inset: 0; }
  .group-name-front {
    position: absolute; left: 44px; top: 108px;
    color: var(--white); font-weight: 700; font-size: 40px;
    letter-spacing: 0.5px;
  }
  .holder {
    position: absolute; right: 37px; top: 28px; text-align: right; color: var(--white);
  }
  .holder-name { font-weight: 600; font-size: 19px; line-height: 1.3; }
  .holder-role { font-weight: 400; font-size: 15px; }
  .contact {
    position: absolute; right: 37px; top: 215px; text-align: right;
    color: var(--white); font-size: 15px; line-height: 21px;
  }
  .contact .address { margin-bottom: 16px; }
  .contact-line { display: flex; justify-content: flex-end; align-items: center; gap: 9px; }
  .contact-line svg { width: 11px; height: 11px; fill: var(--white); }

  /* Back */
  .card-back {
    position: absolute; left: 388px; top: 505px;
    width: 567px; height: 352px;
    background: var(--white);
    overflow: hidden;
    box-shadow: var(--card-shadow);
  }
  .band-block { position: absolute; top: 128px; height: 97px; background: var(--navy); }
  .band-block.left { left: 0; width: 100px; }
  .band-block.right { right: 0; width: 103px; }
  .band-accent { position: absolute; top: 128px; height: 97px; width: 12px; background: var(--green); }
  .band-accent.left { left: 105px; }
  .band-accent.right { right: 107px; }
  .group-name-back {
    position: absolute; left: 118px; right: 118px; top: 152px;
    text-align: center; color: var(--navy); font-weight: 700; font-size: 36px;
  }
  .company-row {
    position: absolute; left: 20px; right: 20px; top: 278px;
    display: flex; justify-content: space-around; align-items: center;
  }
  .company {
    display: flex; align-items: center; gap: 6px;
    color: var(--navy); font-weight: 700; font-size: 14px; white-space: nowrap;
  }
  .company .mark-circle { width: 14px; height: 14px; border-radius: 50%; background: var(--green); }
  .company .mark-square { width: 13px; height: 13px; background: var(--navy); }
</style>
</head>
<body>
<div class="canvas">

  <section class="card-front" aria-label="Business card front">
    <svg class="swoosh" viewBox="0 0 588 364" preserveAspectRatio="none" aria-hidden="true">
      <path d="M0 364 C 120 250, 330 150, 588 196 L588 364 Z" fill="#ffffff"/>
      <path d="M28 364 C 150 262, 350 170, 588 206 L588 364 Z" fill="#80c242"/>
    </svg>
    <div class="group-name-front">Corvanta Group</div>
    <div class="holder">
      <div class="holder-name">Daniel Hartley</div>
      <div class="holder-role">Managing Director</div>
    </div>
    <div class="contact">
      <div class="address">12345, Address Goes Here<br>Country Name, 123456.</div>
      <div class="contact-line">044-123 456 789
        <svg viewBox="0 0 12 12"><path d="M1 4 C1 2 3 1 6 1 C9 1 11 2 11 4 L8.5 5 L8 3.5 L4 3.5 L3.5 5 Z M2.5 6 L9.5 6 L10.5 11 L1.5 11 Z"/></svg>
      </div>
      <div class="contact-line">044-123 456 789
        <svg viewBox="0 0 12 12"><path d="M3 1 L8 1 L8 4 L10 4 L10 11 L2 11 L2 4 L3 4 Z M4 6 L8 6 L8 7 L4 7 Z"/></svg>
      </div>
      <div class="contact-line">info@webname.com
        <svg viewBox="0 0 12 12"><path d="M1 3 L11 3 L11 10 L1 10 Z M1.5 3.5 L6 7 L10.5 3.5" fill="#ffffff" stroke="#80c242" stroke-width="0.8"/></svg>
      </div>
    </div>
  </section>

  <section class="card-back" aria-label="Business card back">
    <div class="band-block left"></div>
    <div class="band-accent left"></div>
    <div class="band-accent right"></div>
    <div class="band-block right"></div>
    <div class="group-name-back">Corvanta Group</div>
    <div class="company-row">
      <div class="company"><span class="mark-circle"></span>Corvanta Roofing</div>
      <div class="company">Kestrel Sheetmetal</div>
      <div class="company"><span class="mark-square"></span>Marlow Forming</div>
      <div class="company">Veltra Panels</div>
    </div>
  </section>

</div>
</body>
</html>
```